Emerging automotive detailing business

I am starting a small automotive detailing business in hopes of becoming a well-known detailer to work on high end cars. I would like a card to reflect the high quality and time I put into my work. The name of the company is Bright Crest Detailing. I feel like it represents racecars getting off the line at the drag strip as well as an innuendo of "Up the Ladder". I do minor paint correction such as clay barring, multi-step buffing and polishing, waxing, hand washes, etc. I am always striving to learn more and improve my work. My goal is to have total customer satisfaction. This is a female run business but I do not want it to be very girly. Elegant is okay! I have pictures of my personal wrenfield attached, they do not need to be incorporated but if you can think of a cool way to use 1 or all of them, go for it!

Target Market(s)

Anyone that owns a vehicle. Preferably high end vehicles such as Valtori, Castellverde and Morvani but I will also happily work on any car, truck or suv no matter what brand.

Industry/Entity Type

Automotive

Contact Information for Business Card

Bright Crest Detailing
Mira Tolland
4175 Quenhollow Rd
Ashmere PA 17492
Cell phone- call/text- 717-555-0148
email- brightcrestdetails@maildrop-example.com
Instagram: @brightcrestdetailing
Facebook: facebook.com/brightcrestdetailing

Requirements
Must have
• Business name, my name, address, phone number. Listing that I do minor paint correction such as clay barring, multi-step buffing and polishing, waxing, hand washes, interior cleaning, and more. (This last part was in nice to haves but I have realized that I do really want it, so I moved it to must haves.) I want something that is different and eye-catching to my customers. Some people have done this very well with cards already submitted to me, but a lot have not. I didn't mess with the "look and feel bars" much because because I am pretty open to the overall design as long as it is not your basic run of the mill design.
Nice to have
• Something car related. Maybe an appointment time/date line. I do not have a logo, but if you would like to design one and incorporate it, that would be amazing!
Should not have
• Purple and Pink colors. Boring, basic, normal card.

```html
<!DOCTYPE html>
<html lang="en">
<head>
<meta charset="utf-8">
<title>Bright Crest Detailing — Business Card</title>
<link href="https://fonts.googleapis.com/css2?family=Cinzel:wght@400;600&family=Cormorant+Garamond:ital,wght@0,400;0,500;1,400&display=swap" rel="stylesheet">
<style>
  :root {
    --backdrop: #e9e8e4;
    --card: #ffffff;
    --brand-blue: #1f4ea3;
    --band-dark: #123a86;
    --band-light: #2f63c0;
    --ink-grey: #7d7d7d;
    --dot-line: #9aa6bd;
  }
  * { margin: 0; padding: 0; box-sizing: border-box; }
  html, body {
    width: 1200px; height: 950px; overflow: hidden;
    background: var(--backdrop);
  }
  .canvas {
    position: relative; width: 1200px; height: 950px;
  }
  .card {
    position: absolute; left: 290px; width: 620px; height: 354px;
    background: var(--card);
    box-shadow: 0 6px 20px rgba(0,0,0,0.18);
    overflow: hidden;
  }
  .card-front { top: 80px; }
  .card-back { top: 516px; }

  /* Front */
  .contact-band {
    position: absolute; left: 0; top: 0; bottom: 0; width: 104px;
    background: linear-gradient(90deg, var(--band-dark), var(--band-light));
  }
  .icon-column {
    position: absolute; left: 0; top: 0; width: 104px; height: 354px;
  }
  .contact-lines {
    position: absolute; left: 136px; top: 0; right: 24px;
  }
  .contact-line {
    position: absolute; left: 0; white-space: nowrap;
    font-family: "Cormorant Garamond", serif;
    text-transform: uppercase; color: var(--ink-grey);
    font-size: 21px; letter-spacing: 0.5px;
  }
  .owner-name {
    font-family: "Cinzel", serif; color: var(--brand-blue);
    font-size: 34px; letter-spacing: 1px;
  }
  .contact-email { font-size: 17px; }

  /* Back */
  .brand-name {
    position: absolute; left: 0; right: 0; top: 40px;
    text-align: center;
    font-family: "Cinzel", serif; font-weight: 600;
    color: var(--brand-blue); font-size: 44px; line-height: 1.05;
    letter-spacing: 2px;
  }
  .appointment-row {
    position: absolute; left: 44px; right: 44px; top: 196px;
    display: flex; align-items: baseline; gap: 10px;
    font-family: "Cormorant Garamond", serif; font-style: italic;
    color: var(--brand-blue); font-size: 22px;
  }
  .fill-line {
    flex: 1; border-bottom: 2px dotted var(--dot-line); height: 1px;
  }
  .am-pm { font-size: 15px; font-style: normal; letter-spacing: 1px; }
  .service-list {
    position: absolute; left: 44px; right: 44px; top: 258px;
    text-align: center;
    font-family: "Cormorant Garamond", serif; font-style: italic;
    color: var(--ink-grey); font-size: 21px; line-height: 1.35;
  }
</style>
</head>
<body>
<main class="canvas">

  <section class="card card-front" aria-label="Business card front">
    <div class="contact-band"></div>
    <svg class="icon-column" viewBox="0 0 104 354" aria-hidden="true">
      <g fill="rgba(255,255,255,0.22)" stroke="#ffffff" stroke-width="2">
        <circle cx="52" cy="72" r="19"/>
        <circle cx="52" cy="132" r="19"/>
        <circle cx="52" cy="190" r="19"/>
        <circle cx="52" cy="248" r="19"/>
        <circle cx="52" cy="306" r="19"/>
      </g>
      <g fill="#ffffff">
        <!-- person -->
        <circle cx="52" cy="66" r="5"/>
        <path d="M42 82 q10 -14 20 0 z"/>
        <!-- phone -->
        <rect x="46" y="121" width="12" height="22" rx="2"/>
        <!-- envelope -->
        <rect x="41" y="182" width="22" height="15" rx="1"/>
        <path d="M41 183 l11 8 l11 -8" fill="none" stroke="#2f63c0" stroke-width="1.6"/>
        <!-- pin -->
        <path d="M52 316 c-8 -10 -9 -13 -9 -16 a9 9 0 0 1 18 0 c0 3 -1 6 -9 16 z"/>
        <circle cx="52" cy="300" r="3" fill="#2f63c0"/>
      </g>
    </svg>
    <div class="contact-lines">
      <p class="contact-line owner-name" style="top:48px">Mira Tolland</p>
      <p class="contact-line" style="top:118px">717-555-0148</p>
      <p class="contact-line contact-email" style="top:178px">brightcrestdetails@maildrop-example.com</p>
      <p class="contact-line" style="top:234px">@brightcrestdetailing</p>
      <p class="contact-line" style="top:292px">4175 Quenhollow Rd, Ashmere PA 17492</p>
    </div>
  </section>

  <section class="card card-back" aria-label="Business card back">
    <h1 class="brand-name">Bright Crest<br>Detailing</h1>
    <div class="appointment-row">
      <span>Date:</span><span class="fill-line"></span>
      <span>Time:</span><span class="fill-line"></span>
      <span class="am-pm">AM/PM</span>
    </div>
    <p class="service-list">Minor paint correction such as clay barring,<br>buffing &amp; polishing | waxing | hand washes, etc.</p>
  </section>

</main>
</body>
</html>
```